Income Tax Flyer - Updates Needed

Just need to update this flyer design and give it a new look. We would like to keep all the same wording but make it stand out a little more. Our selling point is the "Same Day Tax Advance up to $6,000"

Lending, Small Loans, Tax Services, Title Loans, Personal Loans

```html
<!DOCTYPE html>
<html lang="en">
<head>
<meta charset="UTF-8">
<title>Same Day Tax Advance Flyer</title>
<link href="https://fonts.googleapis.com/css2?family=Montserrat:wght@700;800;900&family=Poppins:wght@400;500;600;700&display=swap" rel="stylesheet">
<style>
  :root {
    --green: #2d5131;
    --green-deep: #1f3a23;
    --red: #a8232a;
    --red-bright: #c42b33;
    --cream: #f6f3ec;
    --white: #ffffff;
    --photo-light: #dfe4e6;
    --photo-mid: #aab3bd;
    --photo-dark: #5f6876;
  }
  * { margin: 0; padding: 0; box-sizing: border-box; }
  html, body { width: 859px; height: 1200px; overflow: hidden; background: var(--white); }
  .flyer {
    position: relative;
    width: 859px;
    height: 1200px;
    display: flex;
    flex-direction: column;
    background: var(--cream);
    font-family: 'Poppins', sans-serif;
    color: var(--green);
    overflow: hidden;
  }

  /* Header */
  .brand {
    height: 100px;
    flex: none;
    display: flex;
    align-items: center;
    justify-content: center;
    gap: 14px;
    background: var(--white);
    border-bottom: 6px solid var(--red);
  }
  .brand-mark { width: 20px; height: 20px; border-radius: 50%; background: var(--red); }
  .brand-name { font-weight: 600; font-size: 28px; color: var(--green); letter-spacing: 0.4px; }

  /* Hero */
  .hero {
    position: relative;
    height: 540px;
    flex: none;
    background: linear-gradient(135deg, var(--green) 0%, var(--green-deep) 100%);
    display: flex;
    align-items: center;
    padding: 0 40px 0 48px;
    gap: 32px;
  }
  .hero-copy { width: 420px; flex: none; color: var(--white); }
  .hero-title {
    font-family: 'Montserrat', sans-serif;
    font-weight: 800;
    font-size: 46px;
    line-height: 1.05;
    letter-spacing: 0.5px;
  }
  .hero-rule { width: 90px; height: 6px; background: var(--red-bright); margin: 22px 0 20px; border-radius: 3px; }
  .hero-upto {
    display: inline-block;
    background: var(--red-bright);
    color: var(--white);
    font-family: 'Montserrat', sans-serif;
    font-weight: 800;
    font-size: 26px;
    letter-spacing: 2px;
    padding: 4px 16px;
    border-radius: 6px;
  }
  .hero-amount {
    font-family: 'Montserrat', sans-serif;
    font-weight: 900;
    font-size: 104px;
    line-height: 1;
    margin-top: 10px;
    letter-spacing: -1px;
  }
  .hero-photo {
    flex: 1;
    height: 450px;
    border-radius: 22px;
    border: 6px solid var(--white);
    background: linear-gradient(160deg, var(--photo-light) 0%, var(--photo-mid) 50%, var(--photo-dark) 100%);
  }

  /* Offer band */
  .offer {
    height: 160px;
    flex: none;
    background: var(--red);
    color: var(--white);
    text-align: center;
    display: flex;
    flex-direction: column;
    justify-content: center;
  }
  .offer-lead { font-size: 30px; font-weight: 500; letter-spacing: 0.5px; line-height: 1.3; }
  .offer-emph { font-size: 52px; font-weight: 700; letter-spacing: 1px; line-height: 1.2; }

  /* Features */
  .features {
    height: 230px;
    flex: none;
    display: flex;
    justify-content: center;
    align-items: center;
    gap: 24px;
  }
  .feature {
    width: 240px;
    height: 170px;
    background: var(--white);
    border-radius: 16px;
    border-top: 5px solid var(--red);
    box-shadow: 0 4px 14px rgba(31, 58, 35, 0.10);
    display: flex;
    flex-direction: column;
    align-items: center;
    justify-content: center;
    gap: 12px;
    text-align: center;
  }
  .feature-icon {
    width: 74px; height: 74px;
    border-radius: 50%;
    background: var(--cream);
    border: 2px solid var(--red);
    display: flex;
    align-items: center;
    justify-content: center;
  }
  .feature-label {
    font-size: 19px;
    font-weight: 500;
    line-height: 1.25;
    color: var(--green);
    height: 48px;
    display: flex;
    align-items: center;
  }

  /* Footer */
  .contact-bar {
    flex: 1;
    background: var(--green);
    display: flex;
    align-items: center;
    justify-content: space-between;
    padding: 0 70px 0 90px;
  }
  .cta { text-align: center; }
  .cta-lead { font-size: 30px; font-weight: 600; color: var(--white); line-height: 1.2; }
  .cta-pill {
    margin-top: 6px;
    background: var(--red-bright);
    color: var(--white);
    font-size: 26px;
    font-weight: 700;
    border-radius: 10px;
    line-height: 44px;
    padding: 0 24px;
  }
  .contact {
    font-style: normal;
    padding-left: 28px;
    border-left: 3px solid var(--red-bright);
  }
  .contact-phone { font-size: 22px; font-weight: 700; color: var(--white); line-height: 1.3; margin-bottom: 6px; }
  .contact-line { font-size: 17px; font-weight: 500; color: var(--cream); line-height: 27px; }
</style>
</head>
<body>
<main class="flyer">
  <header class="brand">
    <span class="brand-mark"></span>
    <span class="brand-name">Ledgerline Financial Group</span>
  </header>

  <section class="hero">
    <div class="hero-copy">
      <h1 class="hero-title">SAME DAY<br>TAX ADVANCE</h1>
      <div class="hero-rule"></div>
      <div class="hero-upto">UP TO</div>
      <div class="hero-amount">$6,000</div>
    </div>
    <div class="hero-photo" role="img" aria-label="Photo of a smiling couple meeting with a financial advisor in a bright office"></div>
  </section>

  <section class="offer">
    <div class="offer-lead">File your tax and apply for an</div>
    <div class="offer-emph">Easy Advance!</div>
  </section>

  <section class="features">
    <div class="feature">
      <div class="feature-icon">
        <svg width="48" height="48" viewBox="0 0 54 54" fill="none" stroke="#2d5131" stroke-width="3" stroke-linecap="round">
          <rect x="22" y="3" width="10" height="5" rx="1"/>
          <line x1="27" y1="8" x2="27" y2="12"/>
          <circle cx="27" cy="31" r="19"/>
          <circle cx="27" cy="31" r="13"/>
          <line x1="43" y1="13" x2="46" y2="10"/>
          <line x1="11" y1="13" x2="8" y2="10"/>
          <text x="27" y="37" text-anchor="middle" font-family="Poppins, sans-serif" font-size="16" font-weight="700" fill="#2d5131" stroke="none">$</text>
        </svg>
      </div>
      <div class="feature-label">Available in<br>24 Hours or Less</div>
    </div>

    <div class="feature">
      <div class="feature-icon">
        <svg width="48" height="48" viewBox="0 0 54 54" fill="none" stroke="#2d5131" stroke-width="3" stroke-linecap="round" stroke-linejoin="round">
          <path d="M40 22a17 17 0 1 0-18 17"/>
          <text x="22" y="28" text-anchor="middle" font-family="Poppins, sans-serif" font-size="15" font-weight="700" fill="#2d5131" stroke="none">$</text>
          <path d="M30 48V26a3 3 0 0 1 6 0v10l7 2a4 4 0 0 1 3 4v6"/>
        </svg>
      </div>
      <div class="feature-label">Choose Your<br>Loan Amount</div>
    </div>

    <div class="feature">
      <div class="feature-icon">
        <svg width="48" height="48" viewBox="0 0 54 54" fill="none" stroke="#2d5131" stroke-width="3" stroke-linecap="round" stroke-linejoin="round">
          <rect x="22" y="5" width="22" height="36" rx="2"/>
          <circle cx="33" cy="23" r="6"/>
          <path d="M8 36l10-12a4 4 0 0 1 6 0l4 4-6 8"/>
          <path d="M8 36l8 10"/>
        </svg>
      </div>
      <div class="feature-label">Quick and Easy</div>
    </div>
  </section>

  <footer class="contact-bar">
    <div class="cta">
      <div class="cta-lead">Contact Us</div>
      <div class="cta-pill">Today!</div>
    </div>
    <address class="contact">
      <div class="contact-phone">Phone Number</div>
      <div class="contact-line">Address line 1</div>
      <div class="contact-line">Address line 2</div>
      <div class="contact-line">Address line 3</div>
    </address>
  </footer>
</main>
</body>
</html>
```